Pemberlux: Smart Quotes for Wine Lovers

Hello. I am completing book of quotes for wine lovers. Need the text formatted so that it is easy to read and aesthetically pleasing...modern, clean, smart. Number the pages. The cover is complete. Book is small square. 7.5 by 7.5 inches. If you want to show me first few pages that would be awesome. Thank you!
Updates

I edited the quotes so if you downloaded first ones, please grab these ones instead, thank you! 

Target Market(s)

wine lovers. Urban. Modern.

Industry/Entity Type

Quotes

Requirements
Should not have
• No color. black and white only.

```html
<!DOCTYPE html>
<html lang="en">
<head>
<meta charset="utf-8">
<title>Pemberlux: Smart Quotes for Wine Lovers — Spread 22–23</title>
<link rel="stylesheet" href="https://fonts.googleapis.com/css2?family=Noto+Sans:wght@400;700&display=swap">
<style>
  :root {
    --paper: #ffffff;
    --ink: #000000;
    --note: #8a8a8a;
    --gutter: #c8c8c8;
  }
  html, body {
    margin: 0;
    padding: 0;
    width: 1200px;
    height: 600px;
    overflow: hidden;
    background: var(--paper);
  }
  .spread {
    position: relative;
    width: 1200px;
    height: 600px;
    background: var(--paper);
    color: var(--ink);
    font-family: "Noto Sans", Verdana, sans-serif;
  }
  .gutter {
    position: absolute;
    left: 600px;
    top: 0;
    width: 1px;
    height: 600px;
    background: var(--gutter);
  }
  .page {
    position: absolute;
    top: 0;
    width: 600px;
    height: 600px;
  }
  .page--left { left: 0; }
  .page--right { left: 601px; }

  .quote {
    position: absolute;
    margin: 0;
    font-size: 33px;
    font-weight: 400;
    line-height: 40px;
    letter-spacing: 0.2px;
  }
  .page--left .quote {
    right: 216px;
    top: 208px;
    text-align: right;
  }
  .page--right .quote {
    left: 215px;
    top: 208px;
    text-align: left;
  }
  .attribution {
    position: absolute;
    margin: 0;
    font-size: 13px;
    letter-spacing: 1px;
    text-transform: uppercase;
  }
  .page--left .attribution {
    right: 216px;
    top: 385px;
  }
  .page--right .attribution {
    left: 215px;
    top: 346px;
  }
  .folio {
    position: absolute;
    top: 522px;
    margin: 0;
    font-size: 13px;
  }
  .page--left .folio { left: 78px; }
  .page--right .folio { right: 79px; }

  .footnote {
    position: absolute;
    top: 518px;
    margin: 0;
    font-size: 7.5px;
    font-weight: 700;
    line-height: 10px;
    color: var(--note);
    white-space: nowrap;
  }
  .page--left .footnote {
    right: 63px;
    text-align: right;
  }
  .page--right .footnote {
    left: 61px;
    text-align: left;
  }
</style>
</head>
<body>
  <main class="spread">
    <section class="page page--left">
      <blockquote class="quote">The connoisseur<br>does not drink<br>wine but tastes<br>its secrets</blockquote>
      <p class="attribution">—Aurelio Varga</p>
      <p class="footnote">Aurelio Tomás Benedetto Varga i Solen, Master Printer of<br>Olmen (1912–1981) Iberian Modernist Etcher.</p>
      <p class="folio">22</p>
    </section>

    <div class="gutter" aria-hidden="true"></div>

    <section class="page page--right">
      <blockquote class="quote">Wine is the<br>divine juice of<br>September</blockquote>
      <p class="attribution">—Corvelle</p>
      <p class="footnote">Lucien-Marie Dorvane known by his “nom de plume” Corvelle.<br>(1731 –1802). Lyonnais Salon Essayist, Diarist and Vintner.</p>
      <p class="folio">23</p>
    </section>
  </main>
</body>
</html>
```